Business Card Design Project

Business Card
We are rebranding with a new logo
Industry/Entity Type
Business
Contact Information for Business Card
Dennis Morvale +61 487215963 dennis@quorv.com.au P.O. Box 872 Fernlow QLD 4309
Requirements
Must have
- Logo

```html
<!DOCTYPE html>
<html lang="en">
<head>
<meta charset="utf-8">
<title>Quorv International – Business Card</title>
<link href="https://fonts.googleapis.com/css2?family=Roboto:wght@400;500&family=Roboto+Condensed:wght@700&display=swap" rel="stylesheet">
<style>
  :root {
    --backdrop: #1f1f1f;
    --card: #f2f2f2;
    --brand-blue: #1a8fc9;
    --deep-blue: #0e6f9c;
    --brand-orange: #f28a1e;
    --text: #4a4a4a;
    --rule: #b5b5b5;
    --white: #ffffff;
  }
  html, body {
    margin: 0;
    padding: 0;
    width: 1200px;
    height: 960px;
    overflow: hidden;
    background: var(--backdrop);
  }
  .canvas {
    position: relative;
    width: 1200px;
    height: 960px;
    font-family: "Roboto", Arial, sans-serif;
  }
  .business-card {
    position: absolute;
    left: 314px;
    top: 294px;
    width: 600px;
    height: 343px;
    border-radius: 18px;
    background: var(--card);
    overflow: hidden;
  }
  .brand-name {
    position: absolute;
    right: 30px;
    top: 40px;
    margin: 0;
    text-align: right;
    color: var(--brand-blue);
    font-weight: 500;
    font-size: 30px;
    line-height: 1.15;
    letter-spacing: 1px;
  }
  .holder-name {
    position: absolute;
    left: 25px;
    top: 196px;
    margin: 0;
    font-family: "Roboto Condensed", "Arial Narrow", sans-serif;
    font-weight: 700;
    font-size: 22px;
    color: var(--brand-blue);
    letter-spacing: 0.2px;
  }
  .divider {
    position: absolute;
    left: 26px;
    top: 229px;
    width: 544px;
    height: 1px;
    background: var(--rule);
  }
  .contact-list {
    position: absolute;
    left: 26px;
    top: 246px;
    margin: 0;
    padding: 0;
    list-style: none;
    font-size: 14px;
    color: var(--text);
    line-height: 19px;
  }
  .contact-list li {
    display: flex;
    align-items: center;
    gap: 8px;
  }
  .contact-list svg { width: 14px; height: 14px; fill: var(--brand-blue); }
  .postal-address {
    position: absolute;
    right: 28px;
    top: 248px;
    margin: 0;
    font-style: normal;
    text-align: right;
    font-size: 14px;
    line-height: 19px;
    color: var(--text);
  }
  .footer-band {
    position: absolute;
    left: 0;
    bottom: 0;
    width: 600px;
    height: 28px;
  }
  .web-address {
    position: absolute;
    right: 33px;
    bottom: 6px;
    margin: 0;
    font-size: 14px;
    color: var(--white);
  }
</style>
</head>
<body>
<div class="canvas">
  <article class="business-card">
    <p class="brand-name">Quorv<br>International</p>

    <h1 class="holder-name">DENNIS MORVALE</h1>
    <div class="divider"></div>

    <ul class="contact-list">
      <li>
        <svg viewBox="0 0 24 24" aria-hidden="true"><path d="M6.6 10.8a15.1 15.1 0 0 0 6.6 6.6l2.2-2.2a1 1 0 0 1 1-.25 11.4 11.4 0 0 0 3.6.57 1 1 0 0 1 1 1V20a1 1 0 0 1-1 1A17 17 0 0 1 3 4a1 1 0 0 1 1-1h3.5a1 1 0 0 1 1 1c0 1.25.2 2.45.57 3.57a1 1 0 0 1-.25 1z"/></svg>
        +61 487215963
      </li>
      <li>
        <svg viewBox="0 0 24 24" aria-hidden="true"><path d="M2 5h20v14H2z M3 6l9 7 9-7" fill="var(--brand-blue)"/><path d="M3 6.5l9 6.5 9-6.5" fill="none" stroke="#f2f2f2" stroke-width="1.6"/></svg>
        dennis@quorv.com.au
      </li>
    </ul>

    <address class="postal-address">P.O. Box 872<br>Fernlow QLD 4309</address>

    <svg class="footer-band" viewBox="0 0 600 28" preserveAspectRatio="none" aria-hidden="true">
      <defs>
        <linearGradient id="bandBlue" x1="0" y1="0" x2="0" y2="1">
          <stop offset="0" stop-color="#1ea6df"/>
          <stop offset="1" stop-color="#0b5f88"/>
        </linearGradient>
      </defs>
      <rect x="0" y="11" width="420" height="5" fill="var(--brand-orange)"/>
      <rect x="0" y="16" width="600" height="12" fill="url(#bandBlue)"/>
      <path d="M408 28 Q418 2 430 2 L600 2 L600 28 Z" fill="url(#bandBlue)"/>
    </svg>
    <p class="web-address">www.quorv.com.au</p>
  </article>
</div>
</body>
</html>
```